Building company buisness cards

We are looking for a sharp modern new look for our business cards.We are a New Zealand based company that specialises in house and land packages.We have attached a photo of the current logo and would like to see if it can be improved somehow if needed.We are open to any colours but we have chosen Black and White at this stage. Feel free to change the font and make the logo smarter looking.Play with the colours and see what looks best.We want a card that looks so good know one will want to throw it away!

Target Market(s)

Building profesonals, home buyers

Industry/Entity Type

Building

Contact Information for Business Card

Garrick Tenwood
0275390628
garrickt@hartvale.co.nz

Font styles to use
Serif
Sans Serif

Colors

Designer to choose colors to be used in the design.

Requirements
Must have
• Just the logo on one side and details on the other
• Clean simple looking card
Nice to have
• Round corners and detail like raised or spot UV
• Something that stands out
Should not have
• To title needed, Director etc

```html
<!DOCTYPE html>
<html lang="en">
<head>
<meta charset="utf-8">
<title>Hartvale Business Cards</title>
<link rel="stylesheet" href="https://fonts.googleapis.com/css2?family=Playfair+Display:wght@700&family=Lato:wght@300;400&display=swap">
<style>
  :root {
    --canvas-bg: #d9d9d9;
    --card-white: #f4f4f4;
    --card-black: #0b0b0d;
    --ink-dark: #1a1718;
    --ink-grey: #8a8a8a;
    --ink-light: #ffffff;
    --rule: #6a6a6a;
  }
  * { margin: 0; padding: 0; box-sizing: border-box; }
  html, body {
    width: 1200px;
    height: 900px;
    overflow: hidden;
    background: var(--canvas-bg);
  }
  .stage {
    position: relative;
    width: 1200px;
    height: 900px;
  }
  .card {
    position: absolute;
    width: 540px;
    height: 310px;
    border-radius: 30px;
    display: flex;
    flex-direction: column;
    align-items: center;
    justify-content: center;
    box-shadow: 0 6px 18px rgba(0,0,0,0.18);
  }
  .card--front {
    left: 110px;
    top: 120px;
    background: var(--card-white);
  }
  .card--back {
    left: 550px;
    top: 470px;
    background: var(--card-black);
  }
  .lockup {
    display: flex;
    flex-direction: column;
    align-items: flex-start;
  }
  .brand-name {
    font-family: "Playfair Display", Georgia, serif;
    font-weight: 700;
    font-size: 60px;
    line-height: 1;
    letter-spacing: 0;
  }
  .card--front .brand-name { color: var(--ink-dark); }
  .card--back .brand-name { color: var(--ink-light); font-size: 54px; }
  .tagline {
    font-family: "Lato", Arial, sans-serif;
    font-weight: 300;
    font-size: 19px;
    color: var(--ink-grey);
    letter-spacing: 0.5px;
    margin-top: 8px;
    padding-left: 4px;
  }
  .contact {
    margin-top: 26px;
    text-align: center;
    color: var(--ink-light);
  }
  .contact__name {
    font-family: "Playfair Display", Georgia, serif;
    font-weight: 700;
    font-size: 26px;
    letter-spacing: 0.5px;
  }
  .contact__rule {
    width: 270px;
    height: 1px;
    background: var(--rule);
    margin: 10px auto;
  }
  .contact__line {
    font-family: "Lato", Arial, sans-serif;
    font-weight: 400;
    font-size: 19px;
    line-height: 1.35;
  }
</style>
</head>
<body>
  <main class="stage">
    <section class="card card--front" aria-label="Card front">
      <div class="lockup">
        <span class="brand-name">Hartvale</span>
        <p class="tagline">Houses shaped around you.</p>
      </div>
    </section>

    <section class="card card--back" aria-label="Card back">
      <span class="brand-name">Hartvale</span>
      <div class="contact">
        <p class="contact__name">Garrick Tenwood</p>
        <div class="contact__rule"></div>
        <p class="contact__line">P: 0275390628</p>
        <p class="contact__line">E: garrickt@hartvale.co.nz</p>
      </div>
    </section>
  </main>
</body>
</html>
```